Company Profile for Academic and Study Abroad Services

I am looking for Power Point Design for company Profile . the company is academic and study abroad services. you can visit the website which is www.korvapath.ae . the colour i prefer is Dark Blue + White + Black . you can find all the content for power point and logo and some picture i need you to add it.

Target Market(s)

Students who wants to study abroad. Universities . Learning centre.

Industry/Entity Type

Education

Font styles to use
Serif
Sans Serif

Colors
0555a3
ffffff
000000
aaaaaa

Requirements
Must have
• Must Have Images for each slides.
Nice to have
• infographic. Images related to the study abroad

```html
<!DOCTYPE html>
<html lang="en">
<head>
<meta charset="utf-8">
<title>Korvapath – Company Profile Slides</title>
<link rel="stylesheet" href="https://fonts.googleapis.com/css2?family=Open+Sans:wght@300;400;600;700&family=Oswald:wght@400;500&display=swap">
<style>
:root{
  --backdrop-light:#8b8b8d;
  --backdrop-dark:#6a6a6c;
  --navy:#0a0f9c;
  --blue:#0b3f84;
  --brand-blue:#1b4fa0;
  --charcoal:#45464d;
  --charcoal-deep:#3c3e44;
  --paper:#f6f6f7;
  --white:#ffffff;
  --ink:#1f1f22;
  --yellow:#f6c431;
  --icon-grey:#d3d3d6;
  --rule:#cfcfd3;
  --chart-fill:#7695bb;
  --grid:#cfd3da;
  --cyan:#2ec3d8;
  --red:#ec5050;
  --pale:#dcdcdf;
  --step-1:#c9c9cd;
  --step-2:#a5a5aa;
  --step-3:#707075;
}
*{margin:0;padding:0;box-sizing:border-box}
html,body{width:1200px;height:1200px;overflow:hidden}
body{
  background:radial-gradient(ellipse at 50% 40%,var(--backdrop-light),var(--backdrop-dark));
  font-family:"Open Sans",Arial,sans-serif;
  position:relative;
}
.slide{
  position:absolute;width:500px;height:282px;
  transform:scale(1.08);transform-origin:0 0;
  background:var(--paper);overflow:hidden;
  box-shadow:0 1px 3px rgba(0,0,0,.25);
}
.col-left{left:51px}.col-right{left:615px}
.row-1{top:144px}.row-2{top:472px}.row-3{top:800px}
.abs{position:absolute}

/* header bar */
.slide-header{position:absolute;left:0;top:0;width:500px;height:47px;background:var(--charcoal)}
.slide-title{position:absolute;left:28px;top:15px;color:var(--white);font-weight:700;font-size:13.5px;letter-spacing:.2px}
.slide-number{position:absolute;right:0;top:0;width:102px;height:47px;background:var(--navy);color:var(--white);font-size:24px;font-weight:400;text-align:center;line-height:47px}

.brand-mark{position:absolute;font-weight:700;font-size:6.5px;letter-spacing:.4px;color:var(--blue)}
.brand-mark.on-dark{color:var(--white)}

/* cover */
.cover-photo{position:absolute;inset:0;background:linear-gradient(120deg,#b9b9b9 0%,#8f8f8f 35%,#cfcfcf 60%,#6e6e6e 100%)}
.cover-band{position:absolute;left:0;top:34px}
.cover-square{position:absolute;left:25px;top:40px;width:28px;height:28px;background:var(--blue)}
.cover-name{position:absolute;left:84px;top:44px;font-weight:700;font-size:11px;color:var(--brand-blue)}
.cover-tagline{position:absolute;left:84px;top:59px;font-weight:700;font-size:10px;color:var(--brand-blue)}

/* who we are */
.feature-icon{position:absolute;width:40px;height:40px}
.feature-num{position:absolute;font-family:"Oswald",Impact,sans-serif;font-weight:500;font-size:44px;line-height:44px;color:var(--yellow)}
.feature-text{position:absolute;width:100px;font-size:5.6px;line-height:7.2px;font-weight:600;color:var(--ink)}
.divider{position:absolute;left:311px;top:64px;width:1px;height:200px;background:var(--rule)}
.headline{position:absolute;left:334px;top:86px;font-size:20px;font-weight:400;color:var(--ink);letter-spacing:.2px}
.headline-sub{position:absolute;left:334px;top:107px;font-size:7px;font-weight:600;color:var(--ink)}
.body-copy{position:absolute;font-size:4.6px;line-height:6.3px;font-weight:600;color:var(--ink)}

/* steps */
.steps{position:absolute;left:78px;top:83px;width:343px;height:114px}
.step{position:absolute;top:0;width:114px;height:114px;color:var(--white);text-align:center}
.step-title{margin-top:25px;font-size:15px;font-weight:300}
.step-text{margin:6px auto 0;width:92px;font-size:4.2px;line-height:5.6px;font-weight:600}
.steps-copy{position:absolute;left:72px;top:212px;width:356px;text-align:center;font-size:6.2px;line-height:8.2px;font-weight:600;color:var(--ink)}

/* chart */
.chart{position:absolute;left:0;top:0;width:500px;height:282px}
.legend-swatch{position:absolute;width:18px;height:18px}
.legend-text{position:absolute;width:92px;font-size:4.6px;line-height:6px;font-weight:600;color:var(--ink)}

/* options */
.option-panel{position:absolute;top:0;height:282px;width:250px;color:var(--white);text-align:center}
.option-a{left:0;background:var(--blue)}
.option-b{left:250px;background:var(--charcoal)}
.options-title{position:absolute;left:30px;top:20px;color:var(--white);font-weight:700;font-size:13px;z-index:2}
.option-name{position:absolute;left:0;top:56px;width:250px;font-size:23px;font-weight:300;letter-spacing:5px}
.option-sub{position:absolute;left:0;top:82px;width:250px;font-size:8px;font-weight:600}
.option-rule{position:absolute;left:95px;top:105px;width:60px;height:1px;background:rgba(255,255,255,.7)}
.option-copy{position:absolute;left:40px;width:170px;font-size:4.6px;line-height:6.3px;font-weight:600}

/* thank you */
.closing-bg{position:absolute;inset:0;background:linear-gradient(135deg,var(--charcoal) 0%,var(--charcoal-deep) 50%,var(--charcoal) 100%)}
.closing{position:absolute;left:0;width:500px;text-align:center;color:var(--white)}
.closing-title{top:44px;font-size:36px;line-height:37px;font-weight:400}
.closing-tag{top:144px;font-size:15px;font-weight:400}
.closing-contact{top:168px;font-size:4.8px;line-height:6.4px;font-weight:600}
.closing-social{top:226px;font-size:4.8px;line-height:6.4px;font-weight:600}
</style>
</head>
<body>

<!-- Cover -->
<section class="slide col-left row-1">
  <div class="cover-photo" role="img" aria-label="Black and white photo of smiling graduates in caps and gowns"></div>
  <svg class="cover-band" width="260" height="50" viewBox="0 0 260 50"><polygon points="0,0 242,0 258,50 0,50" fill="#ffffff"/></svg>
  <div class="cover-square"></div>
  <div class="cover-name">KORVAPATH</div>
  <div class="cover-tagline">Universities Entrance Services</div>
</section>

<!-- Who we are -->
<section class="slide col-right row-1">
  <div class="slide-header"><div class="slide-title">WHO WE ARE</div></div>
  <div class="slide-number">01</div>

  <svg class="feature-icon" style="left:38px;top:85px" viewBox="0 0 40 40"><rect x="2" y="26" width="8" height="12" fill="var(--icon-grey)"/><rect x="13" y="18" width="8" height="20" fill="var(--icon-grey)"/><rect x="24" y="9" width="8" height="29" fill="var(--icon-grey)"/></svg>
  <div class="feature-num" style="left:86px;top:83px">01</div>
  <div class="feature-text" style="left:38px;top:129px">Lorem ipsum dolor sit amet, dicit mellus consetetur ut eum, vim probo libris dicunt at.</div>

  <svg class="feature-icon" style="left:163px;top:85px" viewBox="0 0 40 40"><g fill="var(--icon-grey)"><circle cx="20" cy="20" r="12"/><rect x="17" y="3" width="6" height="34"/><rect x="3" y="17" width="34" height="6"/><rect x="17" y="3" width="6" height="34" transform="rotate(45 20 20)"/><rect x="17" y="3" width="6" height="34" transform="rotate(-45 20 20)"/></g><circle cx="20" cy="20" r="5" fill="var(--paper)"/></svg>
  <div class="feature-num" style="left:214px;top:83px">02</div>
  <div class="feature-text" style="left:163px;top:129px">Lorem ipsum dolor sit amet, dicit mellus consetetur ut eum, vim probo libris dicunt at.</div>

  <svg class="feature-icon" style="left:38px;top:177px" viewBox="0 0 40 40"><g fill="var(--icon-grey)"><circle cx="20" cy="13" r="9"/><path d="M3 38 C3 26 12 23 20 23 C28 23 37 26 37 38 Z"/></g></svg>
  <div class="feature-num" style="left:86px;top:175px">03</div>
  <div class="feature-text" style="left:38px;top:222px">Lorem ipsum dolor sit amet, dicit mellus consetetur ut eum, vim probo libris dicunt at.</div>

  <svg class="feature-icon" style="left:163px;top:177px" viewBox="0 0 40 40"><circle cx="16" cy="16" r="11" fill="none" stroke="var(--icon-grey)" stroke-width="5"/><rect x="26" y="22" width="7" height="16" rx="2" fill="var(--icon-grey)" transform="rotate(-45 29 30)"/></svg>
  <div class="feature-num" style="left:214px;top:175px">04</div>
  <div class="feature-text" style="left:163px;top:222px">Lorem ipsum dolor sit amet, dicit mellus consetetur ut eum, vim probo libris dicunt at.</div>

  <div class="divider"></div>
  <div class="headline">HEADLINE</div>
  <div class="headline-sub">Lorem Ipsum Dolor Sit Amet</div>
  <div class="body-copy" style="left:334px;top:139px;width:145px">Lorem ipsum dolor sit amet, ius exerci corpora eu. Per ne meis vocent iudicabit, in oratio graeci atomorum vim, vide habemus docendi ut eam. Cu dolor salutatus efficiendi nam. Debet quaeque nec te. Omittam reprehendunt eu mea, vocent aperiri eum et, ut ius summo dignissim. Pro ne ubique voluptaria, te alia lorem perfecto vix.</div>
  <div class="body-copy" style="left:334px;top:186px;width:145px">Nam dolor latine ornatus id, choro partiendo mei et. Idque facer vidisse id nec, constituam dissentiunt per ex. In nam elitr assueverit, eum te nemore mentitum hendrerit. Eu solum debet minimum qui. Maluisset gloriatur ne eum, ut et dolor clita adversarium. Ex postea petentium comprehensam vel, vim te eligendi intellegat.</div>
  <div class="brand-mark" style="left:450px;top:255px">KORVAPATH</div>
</section>

<!-- What we do -->
<section class="slide col-left row-2">
  <div class="slide-header"><div class="slide-title">WHAT WE DO</div></div>
  <div class="slide-number">02</div>
  <div class="steps">
    <svg width="343" height="114" viewBox="0 0 343 114" style="position:absolute;left:0;top:0">
      <defs><clipPath id="steps-clip"><rect width="343" height="114" rx="7"/></clipPath></defs>
      <g clip-path="url(#steps-clip)">
        <rect width="343" height="114" fill="var(--step-3)"/>
        <polygon points="0,0 229,0 229,50 235,57 229,64 229,114 0,114" fill="var(--step-2)"/>
        <polygon points="0,0 114,0 114,50 120,57 114,64 114,114 0,114" fill="var(--step-1)"/>
      </g>
    </svg>
    <div class="step" style="left:0">
      <div class="step-title">STEP 1</div>
      <div class="step-text">Share your goals, grades and budget with our advisors so we can shortlist the courses and universities that fit you best.</div>
    </div>
    <div class="step" style="left:115px">
      <div class="step-title">STEP 2</div>
      <div class="step-text">We prepare your documents, write strong statements and submit every application on time, then track each reply for you.</div>
    </div>
    <div class="step" style="left:229px">
      <div class="step-title">STEP 3</div>
      <div class="step-text">Once offers arrive we help you choose, apply for your visa, book housing and get ready for your first day abroad.</div>
    </div>
  </div>
  <div class="steps-copy">Lorem ipsum dolor sit amet, ius exerci corpora eu. Per ne meis vocent iudicabit, in oratio graeci atomorum vim, vide habemus docendi ut eam. Cu dolor salutatus efficiendi nam. Debet quaeque nec te. Omittam reprehendunt eu mea, vocent aperiri eum et, ut ius summo dignissim. Pro ne ubique voluptaria, te alia lorem perfecto vix.</div>
  <div class="brand-mark" style="left:452px;top:255px">KORVAPATH</div>
</section>

<!-- Education levels -->
<section class="slide col-right row-2">
  <div class="slide-header"><div class="slide-title">EDUCATION LEVELS</div></div>
  <div class="slide-number">03</div>
  <svg class="chart" viewBox="0 0 500 282" font-family="Open Sans, Arial, sans-serif">
    <g stroke="var(--grid)" stroke-width=".6" stroke-dasharray="2 2">
      <line x1="78" y1="81" x2="444" y2="81"/><line x1="78" y1="110" x2="444" y2="110"/>
      <line x1="78" y1="139" x2="444" y2="139"/><line x1="78" y1="167" x2="444" y2="167"/>
      <line x1="78" y1="81" x2="78" y2="196"/><line x1="111" y1="81" x2="111" y2="196"/>
      <line x1="145" y1="81" x2="145" y2="196"/><line x1="178" y1="81" x2="178" y2="196"/>
      <line x1="211" y1="81" x2="211" y2="196"/><line x1="244" y1="81" x2="244" y2="196"/>
      <line x1="278" y1="81" x2="278" y2="196"/><line x1="311" y1="81" x2="311" y2="196"/>
      <line x1="344" y1="81" x2="344" y2="196"/><line x1="378" y1="81" x2="378" y2="196"/>
      <line x1="411" y1="81" x2="411" y2="196"/><line x1="444" y1="81" x2="444" y2="196"/>
    </g>
    <polygon fill="var(--chart-fill)" points="78,196 78,154 111,135 145,149 178,140 211,128 244,146 278,153 311,143 344,128 378,110 411,121 444,100 444,196"/>
    <g font-size="6" fill="var(--ink)" text-anchor="end" font-weight="600">
      <text x="71" y="83">400</text><text x="71" y="112">300</text><text x="71" y="141">200</text><text x="71" y="169">100</text>
    </g>
    <g font-size="6" fill="var(--ink)" text-anchor="middle" font-weight="600">
      <text x="78" y="210">A</text><text x="111" y="210">B</text><text x="145" y="210">C</text><text x="178" y="210">D</text>
      <text x="211" y="210">E</text><text x="244" y="210">F</text><text x="278" y="210">G</text><text x="311" y="210">H</text>
      <text x="344" y="210">I</text><text x="378" y="210">J</text><text x="411" y="210">K</text><text x="444" y="210">L</text>
    </g>
    <rect x="128" y="116" width="34" height="19" fill="var(--cyan)"/><polygon points="139,135 151,135 145,141" fill="var(--cyan)"/>
    <rect x="261" y="122" width="33" height="19" fill="var(--red)"/><polygon points="272,141 284,141 278,147" fill="var(--red)"/>
    <rect x="360" y="77" width="33" height="20" fill="var(--pale)"/><polygon points="372,97 384,97 378,103" fill="var(--pale)"/>
    <g fill="#5b6b80"><circle cx="145" cy="149" r="2.2"/><circle cx="278" cy="153" r="2.2"/><circle cx="378" cy="110" r="2.2"/></g>
  </svg>
  <div class="legend-swatch" style="left:75px;top:234px;background:var(--cyan)"></div>
  <div class="legend-text" style="left:97px;top:233px">Lorem ipsum dolor sit amet, dicit mellus consetetur ut eum, vim probo libris dicunt at.</div>
  <div class="legend-swatch" style="left:199px;top:234px;background:var(--red)"></div>
  <div class="legend-text" style="left:221px;top:233px">Lorem ipsum dolor sit amet, dicit mellus consetetur ut eum, vim probo libris dicunt at.</div>
  <div class="legend-swatch" style="left:323px;top:234px;background:var(--pale)"></div>
  <div class="legend-text" style="left:345px;top:233px">Lorem ipsum dolor sit amet, dicit mellus consetetur ut eum, vim probo libris dicunt at.</div>
  <div class="brand-mark" style="left:450px;top:255px">KORVAPATH</div>
</section>

<!-- Why choose -->
<section class="slide col-left row-3">
  <div class="option-panel option-a">
    <div class="option-name">OPTION A</div>
    <div class="option-sub">Lorem Ipsum Dolor Sit Amet</div>
    <div class="option-rule"></div>
    <div class="option-copy" style="top:118px">Lorem ipsum dolor sit amet, ius exerci corpora eu. Per ne meis vocent iudicabit, in oratio graeci atomorum vim, vide habemus docendi ut eam. Cu dolor salutatus efficiendi nam. Debet quaeque nec te. Omittam reprehendunt eu mea, vocent aperiri eum et, ut ius summo dignissim. Pro ne ubique voluptaria, te alia lorem perfecto vix.</div>
    <div class="option-copy" style="top:171px">Nam dolor latine ornatus id, choro partiendo mei et. Idque facer vidisse id nec, constituam dissentiunt per ex. In nam elitr assueverit, eum te nemore mentitum hendrerit. Eu solum debet minimum qui. Maluisset gloriatur ne eum, ut et dolor clita adversarium. Ex postea petentium comprehensam vel, vim te eligendi intellegat.</div>
  </div>
  <div class="option-panel option-b">
    <div class="option-name">OPTION B</div>
    <div class="option-sub">Lorem Ipsum Dolor Sit Amet</div>
    <div class="option-rule"></div>
    <div class="option-copy" style="top:118px">Lorem ipsum dolor sit amet, ius exerci corpora eu. Per ne meis vocent iudicabit, in oratio graeci atomorum vim, vide habemus docendi ut eam. Cu dolor salutatus efficiendi nam. Debet quaeque nec te. Omittam reprehendunt eu mea, vocent aperiri eum et, ut ius summo dignissim. Pro ne ubique voluptaria, te alia lorem perfecto vix.</div>
    <div class="option-copy" style="top:171px">Nam dolor latine ornatus id, choro partiendo mei et. Idque facer vidisse id nec, constituam dissentiunt per ex. In nam elitr assueverit, eum te nemore mentitum hendrerit. Eu solum debet minimum qui. Maluisset gloriatur ne eum, ut et dolor clita adversarium. Ex postea petentium comprehensam vel, vim te eligendi intellegat.</div>
  </div>
  <div class="options-title">WHY CHOOSE KORVAPATH</div>
  <div class="brand-mark on-dark" style="left:450px;top:255px">KORVAPATH</div>
</section>

<!-- Thank you -->
<section class="slide col-right row-3">
  <div class="closing-bg" role="img" aria-label="Dark charcoal background with diagonal stripe texture"></div>
  <div class="closing closing-title">THANK<br>YOU</div>
  <div class="closing closing-tag">BE AMONG THE BEST</div>
  <div class="closing closing-contact">Al Noor Street, Harbor View Tower<br>Block C – 12, 3rd Floor<br>UAE- Abu Dhabi<br>+971 2 600 1234 | +971 50 111 2233 | +971 52 444 5566 | +971 50 777 8899<br>www.korvapath.ae<br>info@korvapath.ae</div>
  <div class="closing closing-social">Facebook: korvapath.ae<br>Twitter: korvapath_ae<br>Instagram: korvapath.ae</div>
</section>

</body>
</html>
```